Professional, Attractive, Simple Website Needed!!

We completed the design for our logo.

We need a website built out around this.

Here are a couple samples of how we want ours formatted.

http://brimvoltco.com

http://www.ravelbeam.com/lp/free-quote?LeadSource=Search%20Engine&ProgramName=searchads&experience=qual&language=en&type=brd&gclid=Xk7PLmqwTRZBNVuEYcaHdFgWsLoPeRtQnMxVbCzJaKiOuYtReWqAsDfGhJkLzXcVbNmQwErTyUiOpAsDfGhJkLzX_wcB

http://quorel.co
Updates

Project Deadline Extended
Reason: Extending this deadline due to our delay in providing designers with content for each page. This is coming in next 24 hours.

Project Deadline Extended
Reason: Due to scheduling conflicts and extended travel delays related to Puerto Rico, the deadline has been extended. Your patience is greatly appreciated.

Project Deadline Extended
Reason: Travel and scheduling conflicts have made it impossible to give this project the thorough review it deserves, therefore I am extending the deadline. Thank you for your patience!

Target Market(s)

Home Owners who earn 60k + household annually

Industry/Entity Type

It Professional

Coding

Coded - Design and coding required

Number of Pages Required

5+ page

Font styles to use
Serif

Colors
34a7d8
9bcb3c

Requirements
Must have
• Simple
• Lead form Entry (Ability for visitor to enter Name, number and address for a quote)
• Sleek Design
• Professional
• Testimonials
• Use color Scheme of Design Logo Attached
Nice to have
• Video when site starts
• Like this
• https://www.vidplexa.com/watch?v=Qm8rTbLw3Np&feature=vidplexa.be
Should not have
• Should not include Commercial solar
• Should not include wind power

```html
<!DOCTYPE html>
<html lang="en">
<head>
<meta charset="utf-8">
<title>Brightfield Energy — Switch to Solar Energy</title>
<link href="https://fonts.googleapis.com/css2?family=Roboto:wght@300;400;500;700&family=Questrial&display=swap" rel="stylesheet">
<style>
:root{
  --brand-blue:#34a7d8;
  --brand-green:#9bcb3c;
  --ink:#1e1e1e;
  --body:#3a3a3a;
  --white:#ffffff;
  --night:#0b1424;
  --panel-dark:#1a2330;
  --footer:#262a2f;
  --footer-bar:#1b1e22;
}
*{box-sizing:border-box;margin:0;padding:0}
html,body{width:1200px;height:2644px;overflow:hidden;background:var(--white)}
body{font-family:'Roboto',sans-serif;color:var(--body);position:relative}
.abs{position:absolute}
.center{left:0;width:1200px;text-align:center}

/* Hero */
.hero{position:absolute;left:0;top:0;width:1200px;height:530px;
  background:linear-gradient(180deg,#2b4a7a 0%,#4f6f9d 22%,#c98a5a 32%,#1b2a44 40%,#0d1a30 70%,#050a14 100%);
  clip-path:polygon(0 0,1200px 0,1200px 473px,600px 530px,0 473px)}
.hero-panels{position:absolute;left:0;top:150px;width:1200px;height:380px;
  background:linear-gradient(160deg,#35507a 0%,#1c2f52 40%,#0a1427 100%);
  clip-path:polygon(0 60px,1200px 210px,1200px 380px,0 380px);opacity:.9}
.nav-rule{top:70px;left:0;width:1200px;height:1px;background:rgba(255,255,255,.45)}
.nav a{position:absolute;top:52px;font-family:'Roboto',sans-serif;font-size:10px;color:var(--white);text-decoration:none;letter-spacing:.3px;transform:translateX(-50%)}
.brand{display:flex;flex-direction:column;align-items:center;gap:3px}
.brand-dot{width:30px;height:30px;border-radius:50%;border:2px solid var(--brand-green)}
.brand-name{font-family:'Roboto',sans-serif;font-size:11px;font-weight:500;color:var(--brand-blue);white-space:nowrap}
.hero-title{top:224px;font-family:'Questrial',sans-serif;font-size:23px;font-weight:700;color:var(--white);letter-spacing:1px}
.hero-sub{top:260px;font-family:'Questrial',sans-serif;font-size:23px;color:var(--white);letter-spacing:1px}
.btn{position:absolute;border:1.5px solid var(--white);color:var(--white);font-size:12px;text-align:center;letter-spacing:.5px;background:transparent}
.hero-btn{left:551px;top:331px;width:100px;height:25px;line-height:22px}
.slider-line{top:523px;height:1px;background:#cfcfcf}
.slider-dot{top:518px;width:10px;height:10px;border-radius:50%;border:1px solid #888;background:var(--white)}
.slider-dot.active::after{content:"";position:absolute;left:2px;top:2px;width:4px;height:4px;border-radius:50%;background:#666}

/* Offer */
.section-title{font-family:'Roboto',sans-serif;font-weight:400;font-size:22px;color:var(--ink);letter-spacing:.5px}
.offer-card{position:absolute;top:641px;width:189px;height:189px;text-align:center;padding:24px 10px 0}
.offer-card svg.frame{position:absolute;left:0;top:0}
.offer-icon{display:block;margin:0 auto 8px}
.offer-card h3{font-size:11px;font-weight:700;color:var(--ink);margin-bottom:3px}
.offer-card p{font-size:8.8px;line-height:12px;color:var(--body)}

/* Projects */
.projects{position:absolute;left:0;top:860px;width:1200px;height:406px;
  background:linear-gradient(180deg,#55657d 0%,#b48a6a 35%,#d7a777 48%,#6a6f7d 70%,#2a3446 100%);
  clip-path:polygon(0 0,1200px 0,1200px 315px,600px 406px,0 315px)}
.projects-title{top:886px;color:var(--white)}
.projects-sub{top:917px;font-size:11.5px;color:#f1ece6}
.photo{position:absolute}
.arrow{position:absolute}

/* About */
.about-text{left:372px;top:1328px;width:456px;text-align:center;font-size:11.3px;line-height:17px;color:var(--body)}
.read-more{top:1424px;font-size:11px;font-weight:700;color:var(--ink);text-decoration:underline}

/* Contact */
.contact{position:absolute;left:0;top:1718px;width:1200px;height:376px;
  background:linear-gradient(180deg,#1e3555 0%,#2a3b52 30%,#1c2430 70%,#3a342e 100%);
  clip-path:polygon(0 0,1200px 0,1200px 322px,600px 376px,0 322px)}
.contact-title{top:1744px;color:var(--white)}
.field{position:absolute;left:424px;width:348px;border-bottom:1.5px solid var(--white);color:var(--white);font-size:11.5px;padding-bottom:6px;padding-left:10px}
.send-btn{left:551px;top:2039px;width:99px;height:24px;line-height:21px}

/* Reviews */
.review{position:absolute;text-align:center}
.avatar{border-radius:50%;margin:0 auto 3px}
.review .name{font-size:8.5px;color:var(--body)}
.review .role{font-size:6px;color:#777;margin-bottom:6px}
.review p{font-size:8.6px;line-height:12px;color:var(--ink)}
.review.main .name{font-size:10px}
.review.main p{font-size:10.6px;line-height:15px}

/* Footer */
.footer{position:absolute;left:0;top:2394px;width:1200px;height:250px;
  background:linear-gradient(180deg,#3a3f46 0%,#2a2e34 50%,#1f2328 100%);
  clip-path:polygon(0 36px,600px 0,1200px 36px,1200px 250px,0 250px)}
.footer-info{left:428px;font-size:11.5px;color:var(--white);display:flex;gap:8px;align-items:flex-start}
.follow{left:710px;top:2523px;font-size:11px;color:var(--white);letter-spacing:.5px}
.social{position:absolute;top:2545px;width:12px;height:12px;border:1.5px solid #cfd3d8;border-radius:2px}
.footer-bar{position:absolute;left:0;top:2615px;width:1200px;height:29px;background:var(--footer-bar);color:#d5d5d5;font-size:8.5px;text-align:center;line-height:29px}
</style>
</head>
<body>

<!-- Hero -->
<section class="hero" role="img" aria-label="Photo of solar panel rows under a sunset sky">
  <div class="hero-panels"></div>
</section>
<div class="abs nav-rule"></div>
<nav class="nav">
  <a href="#" style="left:360px">HOME</a>
  <a href="#" style="left:433px">ABOUT US</a>
  <a href="#" style="left:509px">SERVICES</a>
  <a href="#" style="left:689px">GALLERY</a>
  <a href="#" style="left:753px">FAQ</a>
  <a href="#" style="left:827px">CONTACT US</a>
</nav>
<div class="abs brand" style="left:540px;top:12px;width:120px">
  <span class="brand-dot"></span>
  <span class="brand-name">Brightfield Energy</span>
</div>
<h1 class="abs center hero-title">SWITCH TO SOLAR ENERGY</h1>
<p class="abs center hero-sub">ENERGY THAT DOES NOT HIT YOUR WALLET</p>
<a class="btn hero-btn">LEARN MORE</a>
<div class="abs slider-line" style="left:362px;width:215px"></div>
<div class="abs slider-line" style="left:623px;width:215px"></div>
<span class="abs slider-dot" style="left:579px"></span>
<span class="abs slider-dot active" style="left:595px"></span>
<span class="abs slider-dot" style="left:611px"></span>

<!-- Offer -->
<h2 class="abs center section-title" style="top:588px">WE OFER YOU</h2>

<div class="offer-card" style="left:242px">
  <svg class="frame" width="189" height="189" viewBox="0 0 189 189" fill="none">
    <path d="M1 60V1H60M6 60V6H60" stroke="#9fd0ea" stroke-width="1.5"/>
    <path d="M129 1H188V60M129 6H183V60" stroke="#cfe39c" stroke-width="1.5"/>
    <path d="M1 129V188H60M6 129V183H60" stroke="#cfe39c" stroke-width="1.5"/>
    <path d="M129 188H188V129M129 183H183V129" stroke="#9fd0ea" stroke-width="1.5"/>
  </svg>
  <svg class="offer-icon" width="30" height="26" viewBox="0 0 30 26" fill="none" stroke="#34a7d8" stroke-width="1.6">
    <path d="M2 22h8l6 2 10-5-2-3-8 3M2 16h6l6 2h4"/><circle cx="19" cy="7" r="5"/>
  </svg>
  <h3>Ecological cleanliness</h3>
  <p>The production, transportation, installation and use of solar power plants is practically not accompanied by harmful emissions into the atmosphere. Even if they are present to a large extent, then compared to traditional sources of energy - this is almost zero impact on the level of the environment</p>
</div>

<div class="offer-card" style="left:505px">
  <svg class="frame" width="189" height="189" viewBox="0 0 189 189" fill="none">
    <path d="M1 60V1H60M6 60V6H60" stroke="#9fd0ea" stroke-width="1.5"/>
    <path d="M129 1H188V60M129 6H183V60" stroke="#cfe39c" stroke-width="1.5"/>
    <path d="M1 129V188H60M6 129V183H60" stroke="#cfe39c" stroke-width="1.5"/>
    <path d="M129 188H188V129M129 183H183V129" stroke="#9fd0ea" stroke-width="1.5"/>
  </svg>
  <svg class="offer-icon" width="30" height="26" viewBox="0 0 30 26" fill="none" stroke="#34a7d8" stroke-width="1.6">
    <path d="M9 8h12l4 14H5z"/><path d="M12 8l-2-5h10l-2 5"/><path d="M15 12v7M12.5 14h4a1.5 1.5 0 010 3h-3"/>
  </svg>
  <h3>Economical, low operating costs</h3>
  <p>Moving to solar panels as an autonomous energy source, owners of frequent houses receive tangible savings. It is also important that maintenance of solar-powered power systems is characterized by low costs</p>
</div>

<div class="offer-card" style="left:762px">
  <svg class="frame" width="189" height="189" viewBox="0 0 189 189" fill="none">
    <path d="M1 60V1H60M6 60V6H60" stroke="#9fd0ea" stroke-width="1.5"/>
    <path d="M129 1H188V60M129 6H183V60" stroke="#cfe39c" stroke-width="1.5"/>
    <path d="M1 129V188H60M6 129V183H60" stroke="#cfe39c" stroke-width="1.5"/>
    <path d="M129 188H188V129M129 183H183V129" stroke="#9fd0ea" stroke-width="1.5"/>
  </svg>
  <svg class="offer-icon" width="30" height="26" viewBox="0 0 30 26" fill="none" stroke="#34a7d8" stroke-width="1.6">
    <circle cx="17" cy="10" r="8"/><path d="M14 10l2 2 4-4M2 22h8l6 2 8-4"/>
  </svg>
  <h3>Innovative technologies</h3>
  <p>Every year, technologies in the production of solar cells are becoming more sophisticated - thin-film modules are introduced directly into the building materials during the construction stage</p>
</div>

<!-- Projects -->
<section class="projects" role="img" aria-label="Photo of solar panels against a cloudy sunset sky"></section>
<h2 class="abs center section-title projects-title">OUR LAST PROJECTS</h2>
<p class="abs center projects-sub">Solar energy is an actively developing direction in the energy supply of private and public buildings</p>
<svg class="arrow" style="left:243px;top:1040px" width="20" height="38" viewBox="0 0 20 38" fill="none" stroke="#fff" stroke-width="2"><path d="M17 2L3 19l14 17"/></svg>
<svg class="arrow" style="left:937px;top:1040px" width="20" height="38" viewBox="0 0 20 38" fill="none" stroke="#fff" stroke-width="2"><path d="M3 2l14 17L3 36"/></svg>
<div class="photo" style="left:287px;top:965px;width:187px;height:187px;background:linear-gradient(180deg,#cfe2f1 0%,#b9cfe0 45%,#6e8a5a 80%,#4d6b3c 100%)" role="img" aria-label="Photo of a white house with a solar roof"></div>
<div class="photo" style="left:486px;top:977px;width:226px;height:226px;background:linear-gradient(180deg,#8fb6e0 0%,#c35a3c 40%,#8a3c2e 60%,#3f6a2f 100%)" role="img" aria-label="Photo of a red-tiled house with solar panels"></div>
<div class="photo" style="left:724px;top:965px;width:187px;height:187px;background:linear-gradient(180deg,#9cc2e6 0%,#3b5278 40%,#d9c1a8 65%,#4f7d3b 100%)" role="img" aria-label="Photo of a family house with rooftop solar panels"></div>

<!-- About -->
<h2 class="abs center section-title" style="top:1292px">WHO WE ARE</h2>
<p class="abs about-text">Brightfield Energy exists solely to serve and empower its customers. Our constant focus on the customer experience ensures a positive result and, ultimately, saved money. We rely on more than 5 billion US dollars, and together with our installation partners, we helped to install more than 1.6 million solar panels on homes in America. Our partnerships allow us to focus on what's most important, your savings and your ability...</p>
<a class="abs center read-more">Read more</a>
<div class="photo" style="left:428px;top:1467px;width:344px;height:219px;background:linear-gradient(135deg,#5f7f4c 0%,#8a95a8 40%,#3f5678 65%,#6c8a50 100%)" role="img" aria-label="Aerial photo of a neighbourhood of houses with solar roofs"></div>

<!-- Contact -->
<section class="contact" role="img" aria-label="Photo of rows of solar panels on a field"></section>
<h2 class="abs center section-title contact-title">CONTACT US</h2>
<div class="field" style="top:1794px">Name</div>
<div class="field" style="top:1842px">Phone</div>
<div class="field" style="top:1890px">Email</div>
<div class="field" style="top:1985px">Message</div>
<a class="btn send-btn">SEND</a>

<!-- Reviews -->
<h2 class="abs center section-title" style="top:2150px">CUSTOMER REVIEWS</h2>
<svg class="arrow" style="left:243px;top:2239px" width="18" height="34" viewBox="0 0 18 34" fill="none" stroke="#111" stroke-width="2"><path d="M16 2L3 17l13 15"/></svg>
<svg class="arrow" style="left:939px;top:2239px" width="18" height="34" viewBox="0 0 18 34" fill="none" stroke="#111" stroke-width="2"><path d="M2 2l13 15L2 32"/></svg>

<div class="review" style="left:330px;top:2208px;width:128px">
  <div class="avatar" style="width:44px;height:44px;background:#b9b3ad" role="img" aria-label="Customer portrait"></div>
  <div class="name">Mara Delling</div>
  <div class="role">●</div>
  <p>Solar Energy is the way ahead, and Quorel are the best at what they do! Plenty of choices and great service all the way. Very good</p>
</div>
<div class="review main" style="left:504px;top:2219px;width:192px">
  <div class="avatar" style="width:62px;height:62px;background:#8c8f94" role="img" aria-label="Customer portrait"></div>
  <div class="name">Owen Petrak</div>
  <div class="role">●</div>
  <p>Very happy to be working with Brightfield Energy. Very professional, customer-focused, work performed high quality and on schedule. I highly recommend them.</p>
</div>
<div class="review" style="left:732px;top:2208px;width:144px">
  <div class="avatar" style="width:44px;height:44px;background:#a7a29c" role="img" aria-label="Customer portrait"></div>
  <div class="name">Liam Corvath</div>
  <div class="role">●</div>
  <p>Our Brightfield Energy provided us with a great Solar installation experience. They provided us with different financing options and provided an installation plan that met our needs and timing... Now it is time to enjoy the energy savings in $$$. Thank you!</p>
</div>

<!-- Footer -->
<footer class="footer" role="img" aria-label="Dark photo of solar panels"></footer>
<div class="abs brand" style="left:540px;top:2406px;width:120px">
  <span class="brand-dot"></span>
  <span class="brand-name">Brightfield Energy</span>
</div>
<div class="abs footer-info" style="top:2502px">
  <svg width="12" height="14" viewBox="0 0 12 14" fill="none" stroke="#fff" stroke-width="1.3"><path d="M6 13s5-5 5-8A5 5 0 001 5c0 3 5 8 5 8z"/><circle cx="6" cy="5" r="1.8"/></svg>
  <span>Lumenvale, Westmark</span>
</div>
<div class="abs footer-info" style="top:2529px">
  <svg width="14" height="11" viewBox="0 0 14 11" fill="none" stroke="#fff" stroke-width="1.3"><rect x="1" y="1" width="12" height="9"/><path d="M1 1l6 5 6-5"/></svg>
  <span>hello@brightfieldenergy.test</span>
</div>
<div class="abs footer-info" style="top:2553px">
  <svg width="13" height="13" viewBox="0 0 13 13" fill="none" stroke="#fff" stroke-width="1.3"><path d="M3 1l2 3-1.5 1.5a7 7 0 004 4L9 8l3 2-1 2c-5 0-10-5-10-10z"/></svg>
  <span>+10(555)018-42-61<br>+10(555)018-42-62</span>
</div>
<div class="abs follow">FOLLOW US</div>
<span class="social" style="left:712px"></span>
<span class="social" style="left:734px"></span>
<span class="social" style="left:757px"></span>
<div class="footer-bar">© 2017 Brightfield Energy. All Rights Reserved</div>

</body>
</html>
```